Business Card Design For Office Furniture Clearance Company

Kestrel Office Clearance - our company name pretty much explains what we do, we clear offices for high end clients, mainly plc's and large international companies.

We require a nice looking business card that displays professionalism but without being too serious.

It would be nice to see just a little more than a conventional boring business card, make sure you add some flare.

Industry/Entity Type

Office Furniture

Contact Information for Business Card

CARD 1

Mark Holloway
Director
mark@kestrelofficeclearance.co.uk
m: 07700 153928

t: 01632 960418
www.kestrelofficeclearance.co.uk

Kestrel Office Clearance
Unit K4 B
2-8 Fenwick Lane
Ashbury
Northvale
ZZ9 4QT

free office clearances… you cant get better than that.

CARD 2

Peter Radford
Director
peter@kestrelofficeclearance.co.uk
m: 07700 382615

t: 01632 960418

Kestrel Office Clearance
Unit K4 B
2-8 Fenwick Lane
Ashbury
Northvale
ZZ9 4QT

Font styles to use
Sans Serif

Requirements
Must have
• A white background - as we have a blue logo.
Nice to have
• Nice use of the logo - play around with this and dissect it.

```html
<!DOCTYPE html>
<html lang="en">
<head>
<meta charset="utf-8">
<title>Kestrel Office Clearance – Business Card</title>
<link href="https://fonts.googleapis.com/css2?family=Montserrat:wght@400;500;700;800&display=swap" rel="stylesheet">
<style>
  :root {
    --stage: #e9ebee;
    --card-dark: #2a2d34;
    --brand-blue: #1a7fc1;
    --brand-navy: #1e5f99;
    --heading-blue: #1d5d97;
    --faint-blue: #eaf2f9;
    --text-grey: #3d3f44;
    --white: #ffffff;
    --flame-gold: #a8862e;
    --flame-red: #7a2f20;
  }
  * { box-sizing: border-box; margin: 0; padding: 0; }
  html, body {
    width: 1200px; height: 900px; overflow: hidden;
    background: var(--stage);
    font-family: "Montserrat", sans-serif;
  }
  .canvas { position: relative; width: 1200px; height: 900px; }

  .card {
    position: absolute;
    width: 620px; height: 390px;
    border-radius: 26px;
    overflow: hidden;
    box-shadow: 0 14px 30px rgba(0,0,0,.18);
  }

  /* Front */
  .card-front { left: 110px; top: 50px; background: var(--card-dark); }
  .front-emblem {
    position: absolute; left: 165px; top: 62px;
    width: 230px; height: 230px; border-radius: 50%;
    background: var(--brand-blue);
    display: flex; align-items: center; justify-content: center;
    text-align: center; padding: 30px;
  }
  .front-emblem .brand-name {
    color: var(--white); font-weight: 800; font-size: 26px;
    line-height: 1.15; text-transform: uppercase; letter-spacing: .5px;
  }
  .flame-art {
    position: absolute; right: 40px; top: 14px;
    width: 170px; height: 250px;
    border-radius: 20% 80% 40% 60% / 30% 60% 40% 70%;
    background: linear-gradient(165deg, var(--flame-gold) 0%, #95592a 55%, var(--flame-red) 100%);
    opacity: .65;
  }
  .tagline {
    position: absolute; left: 30px; right: 30px; bottom: 34px;
    color: var(--white); font-weight: 500; font-size: 14px;
    letter-spacing: 1.2px; text-transform: uppercase; text-align: center;
    white-space: nowrap;
  }

  /* Back */
  .card-back { left: 470px; top: 470px; background: var(--white); }
  .side-band {
    position: absolute; left: 0; top: 0; bottom: 0; width: 92px;
    background: var(--brand-navy);
  }
  .band-dot {
    position: absolute; left: 46px; top: 52px;
    width: 86px; height: 86px; border-radius: 50%;
    background: var(--brand-blue);
    border: 6px solid var(--white);
  }
  .faint-disc {
    position: absolute; right: -60px; top: 20px;
    width: 280px; height: 280px; border-radius: 50%;
    background: var(--faint-blue);
  }
  .details { position: absolute; left: 152px; top: 38px; right: 24px; }
  .company {
    color: var(--heading-blue); font-weight: 800; font-size: 22px;
    text-transform: uppercase; letter-spacing: .3px; white-space: nowrap;
  }
  .person {
    color: var(--brand-blue); font-weight: 700; font-size: 20px;
    text-transform: uppercase; margin-top: 6px;
  }
  .role {
    color: var(--text-grey); font-size: 13px; text-transform: uppercase;
    letter-spacing: .5px; margin-bottom: 10px;
  }
  .address { font-style: normal; color: var(--text-grey); font-size: 14px; line-height: 1.32; }
  .contacts { list-style: none; margin-top: 6px; color: var(--text-grey); font-size: 14px; }
  .contacts li { display: flex; align-items: center; gap: 9px; line-height: 1.45; }
  .contacts svg { width: 13px; height: 13px; flex: none; fill: var(--brand-blue); }
</style>
</head>
<body>
<main class="canvas">

  <section class="card card-front" aria-label="Card front">
    <div class="front-emblem"><span class="brand-name">Kestrel Office Clearance</span></div>
    <div class="flame-art" role="img" aria-label="Stylised golden flame illustration"></div>
    <p class="tagline">Free office clearances... no catch, no cost</p>
  </section>

  <section class="card card-back" aria-label="Card back">
    <div class="faint-disc"></div>
    <div class="side-band"></div>
    <div class="band-dot"></div>
    <div class="details">
      <h1 class="company">Kestrel Office Clearance</h1>
      <h2 class="person">Mark Holloway</h2>
      <p class="role">Director</p>
      <address class="address">
        Kestrel Office Clearance<br>Unit K4 B<br>2-8 Fenwick Lane<br>Ashbury<br>Northvale<br>ZZ9 4QT
      </address>
      <ul class="contacts">
        <li><svg viewBox="0 0 16 16"><path d="M4 0h8a1 1 0 0 1 1 1v14a1 1 0 0 1-1 1H4a1 1 0 0 1-1-1V1a1 1 0 0 1 1-1zm1 2v10h6V2zm3 11a1 1 0 1 0 0 2 1 1 0 0 0 0-2z"/></svg>07700 153928</li>
        <li><svg viewBox="0 0 16 16"><path d="M3.6 1 6 3.8 4.6 5.6a9 9 0 0 0 5.8 5.8l1.8-1.4L15 12.4l-1.6 2.3C7 15 1 9 1.3 2.6z"/></svg>01632 960418</li>
        <li><svg viewBox="0 0 16 16"><path d="M1 3h14v10H1zm1.5 1.2L8 8.5l5.5-4.3v-.2h-11zM2 5.5V12h12V5.5L8 10z"/></svg>mark@kestrelofficeclearance.co.uk</li>
        <li><svg viewBox="0 0 16 16"><path d="M8 1a7 7 0 1 0 0 14A7 7 0 0 0 8 1zm0 1.3c.8.9 1.5 2.3 1.7 4.2H6.3C6.5 4.6 7.2 3.2 8 2.3zM2.4 7.5h2.6c.1 1.8.6 3.3 1.4 4.5a5.7 5.7 0 0 1-4-4.5zm0-1a5.7 5.7 0 0 1 4-4.5c-.8 1.2-1.3 2.7-1.4 4.5zm3.9 1h3.4c-.2 1.9-.9 3.3-1.700 4.2-.8-.9-1.5-2.3-1.7-4.2zM11 7.5h2.6a5.7 5.7 0 0 1-4 4.5c.8-1.2 1.3-2.7 1.4-4.5zm0-1C10.9 4.7 10.4 3.2 9.6 2a5.7 5.7 0 0 1 4 4.5z"/></svg>www.kestrelofficeclearance.co.uk</li>
      </ul>
    </div>
  </section>

</main>
</body>
</html>
```